Indy Film Production Company/Studio

We need a business card designed from an existing logo. We are a digital studio/production company that caters to creating genre entertainment, like Action, Horror, and martial arts. The card along with the logo will be used to Brand the company from letter heads to banners. The design will also be used for postcards and Brochures. It should be professional and masculine.
Updates

Thank you to all the designers who have participated. I'm narrowing down who it will be. Thank you again.

Target Market(s)

Investors, Networks, Producers, and actors

Industry/Entity Type

Film Production

Contact Information for Business Card

Teodoro Valbuena
Producer/Writer/Director
www.kestrelpicturehouse.example

Requirements
Must have
• Website address, Facebook icon and Twitter icon possibly in the back of the card.
Nice to have
• Logline of Company: Follow The Action.

```html
<!DOCTYPE html>
<html lang="en">
<head>
<meta charset="utf-8">
<title>Kestrel Picture House — Business Card</title>
<link href="https://fonts.googleapis.com/css2?family=Open+Sans:wght@400;600;800&display=swap" rel="stylesheet">
<style>
  :root {
    --backdrop: #e9e7e4;
    --card-black: #0d0d0d;
    --accent-red: #e3202b;
    --ink-white: #f2f2f2;
    --ink-grey: #bdbdbd;
    --divider: #5a5a5a;
  }
  * { box-sizing: border-box; margin: 0; padding: 0; }
  html, body {
    width: 1200px; height: 814px; overflow: hidden;
    background: var(--backdrop);
    font-family: "Open Sans", Arial, sans-serif;
  }
  .canvas {
    width: 1200px; height: 814px;
    display: flex; align-items: center; justify-content: center; gap: 40px;
  }
  .card {
    position: relative;
    width: 540px; height: 309px;
    background: var(--card-black);
    box-shadow: 0 10px 28px rgba(0,0,0,.28);
    overflow: hidden;
  }

  /* Front */
  .card-front .frame {
    position: absolute; inset: 10px;
    border: 1.5px solid var(--accent-red);
  }
  .brand-mark {
    position: absolute; left: 42px; top: 112px; width: 210px;
    color: var(--accent-red); font-weight: 800; text-transform: uppercase;
    line-height: 1.02;
  }
  .brand-mark .brand-line-1 { font-size: 40px; letter-spacing: 1px; display: block; }
  .brand-mark .brand-line-2 { font-size: 20px; letter-spacing: 2px; display: block; }
  .card-front .vertical-rule {
    position: absolute; left: 268px; top: 78px; width: 1px; height: 120px;
    background: var(--divider);
  }
  .contact {
    position: absolute; left: 284px; top: 80px; right: 20px;
  }
  .contact .person-name {
    color: var(--accent-red); font-weight: 600; font-size: 17px;
  }
  .contact .person-role {
    color: var(--ink-white); font-size: 13.5px; margin-top: 2px;
  }
  .contact-list { list-style: none; margin-top: 14px; }
  .contact-list li {
    display: flex; align-items: center; gap: 8px;
    color: var(--ink-white); font-size: 12.5px; margin-bottom: 5px;
    white-space: nowrap;
  }
  .contact-list svg { width: 12px; height: 12px; flex: none; }

  /* Back */
  .camera-photo {
    position: absolute; right: 0; top: 0; width: 290px; height: 309px;
    background: radial-gradient(ellipse at 55% 40%, #6e6e6e 0%, #3a3a3a 38%, #141414 72%, var(--card-black) 100%);
  }
  .social-links {
    position: absolute; left: 60px; top: 40px; display: flex; gap: 3px;
  }
  .social-links span {
    width: 20px; height: 20px; background: var(--ink-grey); border-radius: 2px;
  }
  .card-back .brand-mark {
    left: 150px; top: 180px; width: 260px; color: var(--ink-white);
  }
  .card-back .site-url {
    position: absolute; left: 150px; top: 262px;
    color: var(--ink-white); font-size: 13px; font-weight: 600;
  }
</style>
</head>
<body>
<main class="canvas">

  <section class="card card-front" aria-label="Business card front">
    <div class="frame"></div>
    <div class="brand-mark">
      <span class="brand-line-1">Kestrel</span>
      <span class="brand-line-2">Picture House</span>
    </div>
    <div class="vertical-rule"></div>
    <div class="contact">
      <p class="person-name">Teodoro Valbuena</p>
      <p class="person-role">Producer/Writer/Director</p>
      <ul class="contact-list">
        <li>
          <svg viewBox="0 0 12 12" aria-hidden="true"><path fill="var(--accent-red)" d="M2.4 1 4.2 1 5 3.6 3.8 4.6Q4.8 6.9 7.4 8.2L8.4 7 11 7.8 11 9.6Q10.6 11 9.2 11 1 9.8 1 2.4 1.2 1 2.4 1Z"/></svg>
          555 019 7741
        </li>
        <li>
          <svg viewBox="0 0 12 12" aria-hidden="true"><rect x="0.5" y="2" width="11" height="8" fill="var(--accent-red)"/><path d="M1 2.6 6 6.6 11 2.6" fill="none" stroke="var(--card-black)" stroke-width="1"/></svg>
          hi@kestrelpicturehouse.example
        </li>
        <li>
          <svg viewBox="0 0 12 12" aria-hidden="true"><circle cx="6" cy="6" r="5.5" fill="var(--accent-red)"/><path d="M0.8 6H11.2M6 0.8Q3 6 6 11.2M6 0.8Q9 6 6 11.2" fill="none" stroke="var(--card-black)" stroke-width=".8"/></svg>
          www.kestrelpicturehouse.example
        </li>
      </ul>
    </div>
  </section>

  <section class="card card-back" aria-label="Business card back">
    <div class="camera-photo" role="img" aria-label="Photograph of a professional cinema camera rig on a tripod head"></div>
    <div class="social-links" aria-label="Social profiles">
      <span></span><span></span>
    </div>
    <div class="brand-mark">
      <span class="brand-line-1">Kestrel</span>
      <span class="brand-line-2">Picture House</span>
    </div>
    <p class="site-url">www.kestrelpicturehouse.example</p>
  </section>

</main>
</body>
</html>
```